Rollers & Glides.com

Vertical Business Card with focus on branding with our icon. Information on card will be logo, persons name, position, phone number, email address and website. Use the the name Marcus Pellow, position President, phone number 480.915.2267, email Marcus@rollersandglides-demo.com, website www.rollersandglides-demo.com.

```html
<!DOCTYPE html>
<html lang="en">
<head>
<meta charset="utf-8">
<title>Rollers &amp; Glides.com — Business Card</title>
<link href="https://fonts.googleapis.com/css2?family=Montserrat:wght@700&family=Roboto:wght@400;500&display=swap" rel="stylesheet">
<style>
  :root {
    --stage: #2c2d30;
    --brand-blue: #2a5fb0;
    --brand-blue-deep: #1d4a9c;
    --brand-blue-light: #4a80c2;
    --card-white: #ffffff;
    --ink-grey: #4a4a4a;
    --rule-grey: #6d6d6d;
  }
  * { margin: 0; padding: 0; box-sizing: border-box; }
  html, body {
    width: 1200px; height: 929px; overflow: hidden;
    background: var(--stage);
  }
  .stage {
    position: relative; width: 1200px; height: 929px;
    display: flex; align-items: center; justify-content: center; gap: 40px;
  }
  .card {
    position: relative; width: 520px; height: 297px;
    border-radius: 14px; overflow: hidden;
    box-shadow: 0 12px 30px rgba(0,0,0,.45);
  }

  /* Back */
  .card-back {
    background: linear-gradient(120deg, var(--brand-blue-deep) 0%, var(--brand-blue) 45%, var(--brand-blue-light) 100%);
    display: flex; align-items: center; justify-content: center; gap: 16px;
  }
  .brand-dot {
    width: 36px; height: 36px; border-radius: 50%;
    background: var(--card-white); flex: none;
  }
  .brand-name-back {
    font-family: "Roboto", sans-serif; font-weight: 500;
    font-size: 26px; letter-spacing: 2.5px; color: var(--card-white);
  }

  /* Front */
  .card-front { background: var(--card-white); }
  .brand-mark-front {
    position: absolute; right: 40px; top: 28px;
    display: flex; flex-direction: column; align-items: center; gap: 8px;
  }
  .brand-mark-front .brand-dot {
    width: 84px; height: 84px; background: var(--brand-blue);
  }
  .brand-name-front {
    font-family: "Roboto", sans-serif; font-weight: 500;
    font-size: 15px; letter-spacing: 1px; color: var(--brand-blue);
  }
  .person { position: absolute; left: 40px; right: 40px; top: 142px; }
  .person-name {
    font-family: "Montserrat", sans-serif; font-weight: 700;
    font-size: 25px; color: var(--brand-blue); line-height: 1.1;
  }
  .person-role {
    display: flex; align-items: center; gap: 8px;
    font-family: "Roboto", sans-serif; font-weight: 500;
    font-size: 18px; color: var(--ink-grey); margin-top: 1px;
  }
  .role-rule { flex: 1; height: 1px; background: var(--rule-grey); }
  .contacts {
    position: absolute; left: 50px; top: 204px; list-style: none;
    font-family: "Roboto", sans-serif; font-size: 14.5px; color: var(--ink-grey);
  }
  .contacts li { display: flex; align-items: center; gap: 8px; height: 21px; }
  .contacts svg { width: 13px; height: 13px; fill: var(--brand-blue); flex: none; }
  .edge-band {
    position: absolute; left: 0; right: 0; bottom: 0; height: 10px;
    background: var(--brand-blue-deep);
  }
</style>
</head>
<body>
<main class="stage">
  <section class="card card-back" aria-label="Card back">
    <span class="brand-dot"></span>
    <span class="brand-name-back">Rollers &amp; Glides.com</span>
  </section>

  <section class="card card-front" aria-label="Card front">
    <div class="brand-mark-front">
      <span class="brand-dot"></span>
      <span class="brand-name-front">Rollers &amp; Glides.com</span>
    </div>

    <div class="person">
      <div class="person-name">Marcus Pellow</div>
      <div class="person-role">President <span class="role-rule"></span></div>
    </div>

    <ul class="contacts">
      <li>
        <svg viewBox="0 0 24 24" aria-hidden="true"><path d="M6.6 10.8a15.1 15.1 0 0 0 6.6 6.6l2.2-2.2c.3-.3.7-.4 1-.2 1.1.4 2.3.6 3.6.6.6 0 1 .4 1 1V20c0 .6-.4 1-1 1C10.6 21 3 13.4 3 4c0-.6.4-1 1-1h3.5c.6 0 1 .4 1 1 0 1.3.2 2.5.6 3.6.1.3 0 .7-.2 1z"/></svg>
        480.915.2267
      </li>
      <li>
        <svg viewBox="0 0 24 24" aria-hidden="true"><path d="M2 5h20v14H2zm2 2v.5l8 5 8-5V7l-8 5z"/></svg>
        Marcus@rollersandglides-demo.com
      </li>
      <li>
        <svg viewBox="0 0 24 24" aria-hidden="true"><path d="M12 2a10 10 0 1 0 0 20 10 10 0 0 0 0-20zm6.9 9h-3a15 15 0 0 0-1.3-6 8 8 0 0 1 4.3 6zM12 4c.9 1.2 1.7 3.8 1.9 7h-3.8C10.3 7.8 11.1 5.2 12 4zM9.4 5a15 15 0 0 0-1.3 6h-3a8 8 0 0 1 4.3-6zM5.1 13h3a15 15 0 0 0 1.3 6 8 8 0 0 1-4.3-6zM12 20c-.9-1.2-1.7-3.800-1.9-7h3.8c-.2 3.2-1 5.8-1.9 7zm2.6-1a15 15 0 0 0 1.3-6h3a8 8 0 0 1-4.3 6z"/></svg>
        www.rollersandglides-demo.com
      </li>
    </ul>

    <div class="edge-band"></div>
  </section>
</main>
</body>
</html>
```